Corporate Travel Technology Company needs new Business Card design

We need a new business card design to reflect our re-branded company. Our company is called tolvEn (pronounced tolvenn) and we provide Business Intelligence and mobile travel management solutions for the corporate travel industry. Our multinational customers use our solutions to manage large travel budgets and frequent travellers, as well as to save money and reduce risk. We'd like to see designs that use the blue and green palette as well as our corporate logo (attached below). The design should communicate innovation, insight, forward thinking, contemporary, trusted.

Target Market(s)

Large multinational corporates and Travel Agencies.

Industry/Entity Type

Business

Contact Information for Business Card

Rosalind Mercer
Chief Executive
tolvEn
Phone number - +61 (0)2 8134 2907
Email address - rosalind.mercer@tolven-example.com
Mobile number - +61 (0)438 516 702
www.tolven-example.com

Font styles to use
Other font styles liked:
• Please use font as close to corporate logo as possible

Colors
0255a3
0393ce
00a990
33b8a4
33a6d7
3176b5

Requirements
Must have
• Please include the words;
• Mobile Travel Management
• Accelerating Travel Business Insights
• Use corporate logo - although icon can be stylised if needed

```html
<!DOCTYPE html>
<html lang="en">
<head>
<meta charset="utf-8">
<title>tolvEn business card</title>
<link href="https://fonts.googleapis.com/css2?family=Open+Sans:wght@300;400;600&display=swap" rel="stylesheet">
<style>
  :root {
    --page: #e9e7e3;
    --card: #ffffff;
    --brand-blue: #2aa3dc;
    --slate: #435552;
    --logo-ink: #3e4f4c;
    --pale-mark: #dcdfde;
    --on-dark: #ffffff;
  }
  * { margin: 0; padding: 0; box-sizing: border-box; }
  html, body {
    width: 1200px; height: 902px; overflow: hidden;
    background: var(--page);
    font-family: "Open Sans", Arial, sans-serif;
  }
  .sheet {
    position: relative; width: 1200px; height: 902px;
    display: flex; flex-direction: column; align-items: center;
    justify-content: center; gap: 20px;
  }
  .card {
    position: relative; width: 720px; height: 411px;
    background: var(--card); overflow: hidden;
    box-shadow: 0 6px 18px rgba(0,0,0,0.18);
  }
  /* back */
  .card-back .wordmark {
    position: absolute; left: 150px; top: 140px;
    display: flex; align-items: center; gap: 26px;
  }
  .card-back .wordmark-dot {
    width: 92px; height: 92px; border-radius: 50%;
    background: var(--pale-mark);
  }
  .card-back .wordmark-name {
    font-size: 112px; font-weight: 400; color: var(--logo-ink);
    letter-spacing: -2px; line-height: 1;
  }
  /* front */
  .card-front .bands { position: absolute; inset: 0; }
  .card-front .wordmark {
    position: absolute; left: 300px; top: 70px;
    display: flex; align-items: center; gap: 14px;
  }
  .card-front .wordmark-dot {
    width: 34px; height: 34px; border-radius: 50%;
    background: var(--brand-blue);
  }
  .card-front .wordmark-name {
    font-size: 72px; font-weight: 400; color: var(--logo-ink);
    letter-spacing: -1px; line-height: 1;
  }
  .holder {
    position: absolute; left: 30px; top: 300px; color: var(--on-dark);
  }
  .holder-name { font-size: 34px; font-weight: 600; line-height: 1.1; }
  .holder-role { font-size: 26px; font-weight: 300; line-height: 1.2; }
  .contacts {
    position: absolute; left: 478px; top: 246px; list-style: none;
    color: var(--on-dark); font-size: 15px; font-weight: 300;
  }
  .contacts li {
    display: flex; align-items: center; gap: 10px; height: 27px;
  }
  .contacts svg { width: 16px; height: 16px; flex: none; }
</style>
</head>
<body>
<main class="sheet">
  <section class="card card-back" aria-label="Card back">
    <div class="wordmark">
      <span class="wordmark-dot"></span>
      <span class="wordmark-name">tolvEn</span>
    </div>
  </section>

  <section class="card card-front" aria-label="Card front">
    <svg class="bands" viewBox="0 0 720 411" aria-hidden="true">
      <polygon points="300,228 720,228 720,386 478,386" fill="var(--slate)"/>
      <polygon points="0,228 300,228 478,386 0,386" fill="var(--brand-blue)"/>
    </svg>

    <div class="wordmark">
      <span class="wordmark-dot"></span>
      <span class="wordmark-name">tolvEn</span>
    </div>

    <div class="holder">
      <p class="holder-name">Rosalind Mercer</p>
      <p class="holder-role">Chief Executive</p>
    </div>

    <ul class="contacts">
      <li>
        <svg viewBox="0 0 16 16"><rect width="16" height="16" rx="2" fill="#fff"/><rect x="3" y="6" width="10" height="6" rx="1" fill="var(--slate)"/><rect x="4" y="3" width="8" height="3" fill="var(--slate)"/></svg>
        +61 (0)2 8134 2907
      </li>
      <li>
        <svg viewBox="0 0 16 16"><rect width="16" height="16" rx="2" fill="#fff"/><path d="M5 3c-1 1-1 3 1 6s4 4 5 4l1-2-2-1-1 1c-1-.5-2.5-2-3-3l1-1-1-2z" fill="var(--slate)"/></svg>
        +61 (0)438 516 702
      </li>
      <li>
        <svg viewBox="0 0 16 16"><rect width="16" height="16" rx="2" fill="#fff"/><circle cx="8" cy="8" r="5" fill="none" stroke="var(--slate)" stroke-width="1.4"/><path d="M3 8h10M8 3c-2 3-2 7 0 10M8 3c2 3 2 7 0 10" fill="none" stroke="var(--slate)" stroke-width="1"/></svg>
        www.tolven-example.com
      </li>
      <li>
        <svg viewBox="0 0 16 16"><rect width="16" height="16" rx="2" fill="#fff"/><rect x="3" y="4.5" width="10" height="7" fill="none" stroke="var(--slate)" stroke-width="1.2"/><path d="M3 4.5l5 4 5-4" fill="none" stroke="var(--slate)" stroke-width="1.2"/></svg>
        rosalind.mercer@tolven-example.com
      </li>
    </ul>
  </section>
</main>
</body>
</html>
```